Distribution/Printing company needs a web site to inform prospective customers on what we do.

Distribution/Printing/Packaging company needs a web site to inform prospective customers on what we do. Please look at our direct to consumer web site (under development) for an idea of the product lines we sell: storedev.maplewickhaven.com
Logo files are attached as is a flyer that is under development which contains other information about the company (this is to be used for content- not to be posted as is). The web site should be focused on our business customer base and is not intended to be direct to consumer. Site should have a link to our consumer web site.
Site design should be mobile friendly, or mobile could be redirected to a mobile version. This web site will be strictly informational and will not be designed for any sales transactions.

Target Market(s)

Manufacturing and retail businesses, any other multi-site business that would benefit from centralized pricing and budget controls we can provide (banks, medical/dental offices, educational facilities, etc).

Industry/Entity Type

It Company

Coding

Coded - Design and coding required

Number of Pages Required

5+ page

Requirements
Must have
• 1) Top level menu: Products, about us, locations, contact us, news
• 2) page with news/promotions that is easily updated
• 3) "contact us" form (name, company, phone, email address) email link
• 4) link to www.store.maplewickhaven.com with information that lower pricing is available for businesses
• 5) SEO keywords
• 6) Link to powerpoint presentation file
Nice to have
• 1) our phone number should appear on every page near the top

```html
<!DOCTYPE html>
<html lang="en">
<head>
<meta charset="utf-8">
<title>Maplewick Haven Supply – Packaging, Printing, Distribution</title>
<link rel="stylesheet" href="https://fonts.googleapis.com/css2?family=Titillium+Web:wght@300;400;600;700&family=Open+Sans:wght@400;600&display=swap">
<style>
:root{
  --ink:#111111;
  --text:#333333;
  --muted:#555555;
  --white:#ffffff;
  --rule:#dddddd;
  --footer:#2b2b2b;
  --footer-base:#1f1f1f;
  --footer-text:#9a9a9a;
  --btn:#151515;
  --caption:rgba(40,36,30,.82);
  --tile-bar:rgba(0,0,0,.78);
}
*{margin:0;padding:0;box-sizing:border-box}
html,body{width:1200px;height:2719px;overflow:hidden;background:var(--white)}
body{position:relative;font-family:"Open Sans",Arial,sans-serif;color:var(--text)}
.abs{position:absolute}

/* header */
.site-header{left:0;top:0;width:1200px;height:120px;background:var(--white)}
.brand{left:100px;top:12px;width:320px}
.brand-mark{width:22px;height:22px;background:var(--ink);margin-bottom:30px}
.brand-name{font-family:"Titillium Web",sans-serif;font-weight:700;font-size:19px;color:var(--ink);letter-spacing:.2px;line-height:1.1;white-space:nowrap}
.brand-tag{font-family:"Titillium Web",sans-serif;font-weight:700;font-size:13px;color:var(--ink);line-height:1.4;white-space:nowrap}
.main-nav{left:0;top:56px;width:1200px}
.main-nav a{position:absolute;font-family:"Open Sans",sans-serif;font-size:15px;color:var(--ink);text-decoration:none;letter-spacing:.2px}

/* hero */
.hero{left:0;top:120px;width:1200px;height:456px;background:linear-gradient(120deg,#3b2c1e 0%,#6d5337 35%,#9a8a66 55%,#5a4a36 80%,#2d2218 100%)}
.hero-caption{left:100px;top:372px;width:353px;height:172px;background:var(--caption);padding:18px 28px}
.hero-caption h1{font-family:"Titillium Web",sans-serif;font-weight:600;font-size:52px;line-height:1;color:var(--white)}
.hero-caption p{font-size:13.5px;line-height:1.55;color:#e8e8e8;margin-top:12px}
.slider-dots{position:absolute;left:30px;top:138px;display:flex;gap:10px}
.slider-dots span{width:8px;height:8px;border:1px solid #ddd;border-radius:50%}
.slider-dots span.on{background:#ddd}

/* service tiles */
.service-tile{top:589px;width:332px;height:214px}
.service-tile .label{position:absolute;left:0;bottom:0;width:100%;height:45px;background:var(--tile-bar);color:var(--white);font-family:"Titillium Web",sans-serif;font-size:21px;padding:8px 11px}
.tile-shadow{top:803px;width:332px;height:58px;background:radial-gradient(ellipse at 50% 0%,rgba(0,0,0,.28) 0%,rgba(0,0,0,.08) 45%,rgba(255,255,255,0) 70%)}

/* welcome */
.welcome-photo{left:100px;top:883px;width:332px;height:250px;border:1px solid var(--rule);padding:5px;background:var(--white)}
.welcome-photo div{width:100%;height:100%;background:linear-gradient(135deg,#d6a865,#b07a3c 50%,#8a8a88)}
.intro-block{top:878px}
.intro-block .kicker{font-family:"Titillium Web",sans-serif;font-size:20px;color:var(--ink);line-height:1.2}
.intro-block h2{font-family:"Titillium Web",sans-serif;font-weight:400;font-size:31px;color:var(--ink);line-height:1.15}
.intro-block p{font-size:11px;line-height:1.75;color:var(--muted);margin-top:12px}
.btn-dark{display:inline-block;background:var(--btn);color:var(--white);font-size:11px;padding:8px 9px;border-radius:3px;text-decoration:none}
.benefit-list{list-style:none;margin-top:12px}
.benefit-list li{display:flex;align-items:center;gap:8px;font-size:11.5px;color:var(--ink);height:20.5px}

/* bands */
.band{left:0;width:1200px;text-align:center;color:var(--white)}
.band h2{font-family:"Titillium Web",sans-serif;font-weight:400;font-size:31px;color:var(--white)}
.band p{font-size:12px;line-height:1.7;margin:6px auto 0}
.btn-outline{display:inline-block;border:1px solid #e0e0e0;color:var(--white);font-size:12.5px;padding:7px 11px;text-decoration:none}
.band-supply{top:1202px;height:239px;background:linear-gradient(90deg,#3a3230 0%,#5a4f48 35%,#6b5e4d 60%,#4c4538 100%)}
.band-inventory{top:1797px;height:237px;background:linear-gradient(100deg,#101010 0%,#252525 45%,#3a3a36 75%,#1a1a1a 100%)}

/* products */
.section-title{font-family:"Titillium Web",sans-serif;font-weight:400;font-size:30px;color:var(--ink)}
.product-card{top:1550px;width:156px;height:191px;border:1px solid var(--rule);text-align:center}
.product-card .thumb{width:120px;height:110px;margin:16px auto 0;border-radius:4px}
.product-card span{display:block;font-size:12.5px;color:var(--ink);margin-top:20px}

/* features */
.feature{top:2137px;width:238px}
.feature .thumb{height:165px}
.feature span{display:block;width:200px;font-size:14px;color:var(--ink);line-height:1.45;margin-top:19px}

/* footer */
.site-footer{left:0;top:2397px;width:1200px;height:250px;background:var(--footer)}
.footer-base{left:0;top:2647px;width:1200px;height:72px;background:var(--footer-base);color:#777;font-size:11px;text-align:center;line-height:72px}
.footer-col{top:2430px}
.footer-col h3{font-family:"Titillium Web",sans-serif;font-weight:400;font-size:21px;color:var(--white);margin-bottom:9px}
.footer-col a,.footer-col li{display:block;list-style:none;font-size:11px;color:var(--footer-text);text-decoration:none;line-height:21px}
.footer-col p{font-size:11px;color:var(--footer-text);line-height:1.85}
.mail-input{width:184px;height:34px;background:var(--white);border:none;margin-top:14px;font-size:11px;padding:0 10px;color:#333;display:flex;align-items:center}
.btn-submit{display:inline-block;background:#111;color:var(--white);font-size:11px;padding:6px 14px;border-radius:3px;margin-top:17px}
.social li{display:flex;align-items:center;gap:7px}
.social i{width:10px;height:10px;background:var(--footer-text);display:inline-block}
</style>
</head>
<body>

<header class="abs site-header">
  <div class="abs brand">
    <div class="brand-mark"></div>
    <div class="brand-name">MAPLEWICK HAVEN SUPPLY</div>
    <div class="brand-tag">Packaging • Printing • Distribution</div>
  </div>
  <nav class="abs main-nav">
    <a style="left:540px" href="#">HOME</a>
    <a style="left:640px" href="#">ABOUT US</a>
    <a style="left:765px" href="#">SERVICES</a>
    <a style="left:887px" href="#">PRODUCTS</a>
    <a style="left:1019px" href="#">CONTACT US</a>
  </nav>
</header>

<section class="abs hero" role="img" aria-label="Two warehouse workers in hard hats and safety vests reviewing a laptop on cardboard boxes"></section>
<div class="abs hero-caption">
  <h1>Distribution</h1>
  <p>Nemo enim ipsam voluptatem quia voluptas sit aspernatur aut</p>
  <div class="slider-dots"><span></span><span class="on"></span><span></span></div>
</div>

<div class="abs service-tile" style="left:100px;background:linear-gradient(160deg,#6c7f86,#8a8f5a 50%,#4b4a3a)" role="img" aria-label="Warehouse aisle with a forklift moving palletised goods"><div class="label">Distribution</div></div>
<div class="abs service-tile" style="left:435px;background:linear-gradient(160deg,#3a4a44,#6e8a7e 45%,#8e7c8a)" role="img" aria-label="Printed sheets running through a printing press"><div class="label">Printing</div></div>
<div class="abs service-tile" style="left:770px;background:linear-gradient(160deg,#8a6a58,#b9967c 50%,#c9aa8c)" role="img" aria-label="Hands sealing a cardboard box with a tape dispenser"><div class="label">Packaging</div></div>
<div class="abs tile-shadow" style="left:100px"></div>
<div class="abs tile-shadow" style="left:435px"></div>
<div class="abs tile-shadow" style="left:770px"></div>

<div class="abs welcome-photo"><div role="img" aria-label="Cardboard boxes moving along a roller conveyor"></div></div>
<div class="abs intro-block" style="left:446px;width:355px">
  <div class="kicker">Welcome to</div>
  <h2>Maplewick Haven Supply</h2>
  <p>Nemo enim ipsam voluptatem quia voluptas sit aspernatur aut odit aut fugit, sed quia consequuntur magni dolores eos qui ratione voluptatem sequi nesciunt.</p>
  <p style="margin-top:20px">Neque porro quisquam est, qui dolorem ipsum quia dolor sit amet, consectetur, adipisci velit, sed quia non numquam eius</p>
  <a class="btn-dark" href="#" style="margin-top:31px">Read More</a>
</div>
<div class="abs intro-block" style="left:832px;width:270px">
  <div class="kicker">Our</div>
  <h2>Benefits</h2>
  <p>Nemo enim ipsam voluptatem quia voluptas sit aspernatur aut odit aut fugit,</p>
  <ul class="benefit-list">
    <li><svg width="12" height="12" viewBox="0 0 12 12"><circle cx="6" cy="6" r="5.5" fill="#111"/><path d="M3.5 6h4.5M6 3.8L8.2 6 6 8.2" stroke="#fff" stroke-width="1.3" fill="none"/></svg>Control your Spend</li>
    <li><svg width="12" height="12" viewBox="0 0 12 12"><circle cx="6" cy="6" r="5.5" fill="#111"/><path d="M3.5 6h4.5M6 3.8L8.2 6 6 8.2" stroke="#fff" stroke-width="1.3" fill="none"/></svg>Eliminate Rogue Spend</li>
    <li><svg width="12" height="12" viewBox="0 0 12 12"><circle cx="6" cy="6" r="5.5" fill="#111"/><path d="M3.5 6h4.5M6 3.8L8.2 6 6 8.2" stroke="#fff" stroke-width="1.3" fill="none"/></svg>Improve Cash Flow</li>
    <li><svg width="12" height="12" viewBox="0 0 12 12"><circle cx="6" cy="6" r="5.5" fill="#111"/><path d="M3.5 6h4.5M6 3.8L8.2 6 6 8.2" stroke="#fff" stroke-width="1.3" fill="none"/></svg>Prevent Spending Abuse</li>
  </ul>
  <a class="btn-dark" href="#" style="margin-top:16px">Read More</a>
</div>

<section class="abs band band-supply" role="img" aria-label="Dimmed warehouse shelving with workers in hard hats">
  <h2 style="margin-top:48px">Supply Chain Management</h2>
  <p>Are your Procurement Professionals managing transactional purchases across multiple locations, departments, or business units?</p>
  <a class="btn-outline" href="#" style="margin-top:14px">Read More</a>
</section>

<h2 class="abs section-title" style="left:97px;top:1475px">Feature Products</h2>
<div class="abs product-card" style="left:100px"><div class="thumb" role="img" aria-label="Box of clear push pins" style="background:linear-gradient(#eef0f2,#c9ced4)"></div><span>PUSH PINS CLEAR</span></div>
<div class="abs product-card" style="left:269px"><div class="thumb" role="img" aria-label="Case of tissue rolls" style="background:linear-gradient(#f2f4f8,#b8c6dc)"></div><span>TISSUE</span></div>
<div class="abs product-card" style="left:438px"><div class="thumb" role="img" aria-label="Coloured stacking storage bins" style="background:linear-gradient(90deg,#c83a2e,#e0c42e,#2f62b0)"></div><span>Storage</span></div>
<div class="abs product-card" style="left:606px"><div class="thumb" role="img" aria-label="Open cardboard shipping boxes" style="background:linear-gradient(#d7a860,#a9773d)"></div><span>Packaging</span></div>
<div class="abs product-card" style="left:775px"><div class="thumb" role="img" aria-label="Assorted light bulbs" style="background:linear-gradient(#f4f4f4,#c4c8cc)"></div><span>Retail</span></div>
<div class="abs product-card" style="left:944px"><div class="thumb" role="img" aria-label="Calculator and desk office supplies" style="background:linear-gradient(#d8d2c6,#6a6660)"></div><span>Office</span></div>

<section class="abs band band-inventory" role="img" aria-label="Dark close-up of a hand scanning stock">
  <h2 style="margin-top:41px">Inventory Count</h2>
  <p style="width:940px">Supplement inventory counts with an auto-reorder function.&nbsp; I.e. once an item drops below a pre-established minimum inventory level, automatically generate an order for said item to bring counts to pre-set level.</p>
  <a class="btn-outline" href="#" style="margin-top:14px">Read More</a>
</section>

<h2 class="abs section-title" style="left:97px;top:2063px">Our Features</h2>
<div class="abs feature" style="left:100px"><div class="thumb" role="img" aria-label="Stacked cardboard boxes on a pallet jack" style="background:linear-gradient(135deg,#b48a5a,#7a5a3a)"></div><span>Budget Controls at Corporate level</span></div>
<div class="abs feature" style="left:355px"><div class="thumb" role="img" aria-label="Hands typing on a keyboard beside a packing box" style="background:linear-gradient(135deg,#c9a47c,#8a7a6a)"></div><span>Order Restrictions</span></div>
<div class="abs feature" style="left:609px"><div class="thumb" role="img" aria-label="Forklift in a warehouse" style="background:linear-gradient(135deg,#8a7048,#3a3428 60%,#c9a030)"></div><span>Multi-level Approvals</span></div>
<div class="abs feature" style="left:862px"><div class="thumb" role="img" aria-label="Hands taping a cardboard box" style="background:linear-gradient(135deg,#9a7a68,#c8a88a)"></div><span>Order Cycle Management</span></div>

<footer class="abs site-footer"></footer>
<div class="abs footer-col" style="left:97px">
  <h3>Quick Links</h3>
  <a href="#">Home</a><a href="#">About us</a><a href="#">services</a><a href="#">Products</a><a href="#">Contact us</a>
</div>
<div class="abs footer-col" style="left:243px">
  <h3>Products</h3>
  <a href="#">Packaging</a><a href="#">Office</a><a href="#">Storage</a><a href="#">Retail</a><a href="#">Industrial</a>
</div>
<div class="abs footer-col" style="left:430px;width:230px">
  <h3>Subscribe Newsletter</h3>
  <p>Do you want to get email updates from a website or blog</p>
  <div class="mail-input">Enter Your mail ID</div>
  <span class="btn-submit">Submit</span>
</div>
<div class="abs footer-col" style="left:730px;width:220px">
  <h3>Contact us</h3>
  <p>Nemo enim ipsam voluptatem quia volup-tas sit aspernatur</p>
  <p style="margin-top:22px">1800-555-0142</p>
</div>
<div class="abs footer-col" style="left:1020px">
  <h3>Follow us</h3>
  <ul class="social"><li><i></i>Friendsphere</li><li><i></i>Chirpline</li><li><i></i>RSS</li></ul>
</div>
<div class="abs footer-base">© 2015 Maplewick Haven Supply. All rights reserved.</div>

</body>
</html>
```